Modern design company business card design

We are a design oriented construction firm. The owner is an architect and licensed General Contractor and accomplished furniture designer. We do new home construction and large scale remodeling and office design. We would like a design for our new business cards that is clean and modern, but relatable. We like the bright green color of our logo mixed with different shades of grey. We're also open to reinterpreting the logo.

Target Market(s)

Potential design clients,
Construction clients

Industry/Entity Type

Architecture

Contact Information for Business Card

Tall Maple Design | Build Inc. (optional with logo, Inc. optional)Jeffrey MorganOwner (optional)317.555.0148 cell317.431.8056 officejmorgan@greensquareinc.comwww.greensquareinc.com

Font styles to use
Sans Serif
Other font styles liked:
• Avenir

Requirements
Nice to have
• I like designs that have some continuity between the front and back, i.e. similar layouts or graphic elements that wrap around the card. I tend to prefer horizontal over vertical, but that's not a have to. I also tend to prefer white or recycled paper.

```html
<!DOCTYPE html>
<html lang="en">
<head>
<meta charset="utf-8">
<title>Tall Maple Design | Build — Business Card</title>
<link rel="stylesheet" href="https://fonts.googleapis.com/css2?family=Mulish:wght@400;600;700&display=swap">
<style>
  :root {
    --backdrop: #5a3419;
    --paper: #ffffff;
    --grey-light: #6a6b6f;
    --grey-dark: #404145;
    --green: #3aa84a;
    --green-deep: #1f8a34;
    --green-soft: #6fc47e;
    --lime: #b5d96a;
    --lime-pale: #d3e98c;
    --ink-muted: #9a9a9a;
    --tab-note: #c9ecb0;
  }
  html, body {
    margin: 0;
    width: 1200px;
    height: 913px;
    overflow: hidden;
    background: var(--backdrop);
  }
  .stage {
    position: relative;
    width: 1200px;
    height: 913px;
    font-family: "Mulish", sans-serif;
  }
  .card {
    position: absolute;
    width: 520px;
    height: 297px;
    border-radius: 16px;
    overflow: hidden;
    box-shadow: 0 14px 30px rgba(0,0,0,0.35);
  }
  .card svg { display: block; }
  .card--front { left: 70px; top: 150px; }
  .card--back { left: 610px; top: 466px; }
  .brand-name { font-family: "Mulish", sans-serif; font-weight: 600; letter-spacing: 2px; }
  .contact-text { font-family: "Mulish", sans-serif; font-size: 13px; fill: var(--paper); }
  .person-name { font-family: "Mulish", sans-serif; font-weight: 700; font-size: 16px; fill: var(--paper); }
  .person-role { font-family: "Mulish", sans-serif; font-size: 11px; fill: var(--tab-note); }
</style>
</head>
<body>
<div class="stage">

  <!-- Front side -->
  <div class="card card--front">
    <svg width="520" height="297" viewBox="0 0 520 297">
      <defs>
        <linearGradient id="greyFade" x1="0" y1="0" x2="0" y2="1">
          <stop offset="0" stop-color="var(--grey-light)"/>
          <stop offset="1" stop-color="var(--grey-dark)"/>
        </linearGradient>
      </defs>
      <rect class="paper" width="520" height="297" fill="var(--paper)"/>
      <polygon class="accent-band" points="0,170 286,170 316,132 520,132 520,140 320,140 290,178 0,178" fill="var(--green)"/>
      <polygon class="grey-panel" points="0,178 290,178 320,140 520,140 520,297 0,297" fill="url(#greyFade)"/>
      <polygon class="name-tab" points="322,94 520,94 520,140 380,140 366,152 352,140 322,140" fill="var(--green)"/>

      <circle class="brand-dot" cx="46" cy="132" r="9" fill="var(--green)"/>
      <text class="brand-name" x="64" y="140" font-size="22" fill="var(--ink-muted)">TALL MAPLE</text>
      <text class="brand-name" x="65" y="156" font-size="10" fill="var(--ink-muted)">DESIGN | BUILD</text>

      <text class="person-name" x="506" y="117" text-anchor="end">DENNIS HOLLOWAY</text>
      <text class="person-role" x="506" y="133" text-anchor="end">Owner</text>

      <g class="contact-list">
        <rect x="32" y="194" width="12" height="12" rx="2" fill="var(--green)"/>
        <text class="contact-text" x="52" y="205">317.555.0172</text>
        <rect x="32" y="213" width="12" height="12" rx="2" fill="var(--green)"/>
        <text class="contact-text" x="52" y="224">317.555.0148</text>
        <rect x="32" y="232" width="12" height="12" rx="2" fill="var(--green)"/>
        <text class="contact-text" x="52" y="243">www.tallmapleinc.example</text>
        <rect x="32" y="251" width="12" height="12" rx="2" fill="var(--green)"/>
        <text class="contact-text" x="52" y="262">dholloway@tallmapleinc.example</text>
      </g>
    </svg>
  </div>

  <!-- Back side -->
  <div class="card card--back">
    <svg width="520" height="297" viewBox="0 0 520 297">
      <defs>
        <linearGradient id="greenField" x1="0" y1="1" x2="1" y2="0">
          <stop offset="0" stop-color="var(--green-deep)"/>
          <stop offset="1" stop-color="var(--green-soft)"/>
        </linearGradient>
        <linearGradient id="limeField" x1="0" y1="1" x2="1" y2="0">
          <stop offset="0" stop-color="var(--lime)"/>
          <stop offset="1" stop-color="var(--lime-pale)"/>
        </linearGradient>
      </defs>
      <rect class="green-field" width="520" height="297" fill="url(#greenField)"/>
      <polygon class="white-band" points="0,196 250,196 262,156 520,156 520,60 520,60 520,68 0,68" fill="none"/>
      <polygon class="white-band" points="0,200 256,200 268,164 300,70 520,70 520,80 308,80 276,204 264,240 0,240" fill="var(--paper)"/>
      <polygon class="lime-field" points="0,240 264,240 276,204 308,80 520,80 520,297 0,297" fill="url(#limeField)"/>

      <circle class="brand-dot" cx="50" cy="116" r="9" fill="var(--paper)"/>
      <text class="brand-name" x="68" y="124" font-size="21" fill="var(--paper)">TALL MAPLE</text>
      <text class="brand-name" x="69" y="140" font-size="10" fill="var(--paper)">DESIGN | BUILD</text>
    </svg>
  </div>

</div>
</body>
</html>
```